Toms welding and seed cleaning Business cards

Jakes welding and seed cleaningWe clean wheat seed on farm with portable cleaners so the farmers have pure wheat seed to plant back for the next crop. We are certified to clean foundation, registered, and certified seed wheat. Our cleaners being portable make it easier for the farmers because we do it right on there farm so they don't have to haul it all to townWhen there is no wheat to clean we weld in the winter. We improve, add onto, and build new corrals. We also build sheds, cattle shelters, and wind breaks. Other welding is welcomed

Reason: I need to extend the deadline because I've been busy and not had my game together. I need more time figure out what I want yet

Industry/Entity Type

Agriculture

Contact Information for Business Card

Just "toms welding and seed cleaning" on front and other info on the back
On the back side I would like to have my address.
Morris Tulane
48213 W COUNTY RD 318
CEDAR BEND OK 73990
Phone #5804419362

Font styles to use
Sans Serif

Requirements
Must have
• list we are certified to clean foundation, registered, and certified wheat
• State that they are portable cleaners
• For the welding part list, add on to, improve on, and repair existing corrals and new corrals and other welding welcomed
Nice to have
• A wheat field with some metal corrals on the side with a nice classic looking barn for a background. Maybe some cattle in the corrals
• A nice looking farm yard would be good too

```html
<!DOCTYPE html>
<html lang="en">
<head>
<meta charset="utf-8">
<title>Toms Welding And Seed Cleaning – Business Card</title>
<link rel="stylesheet" href="https://fonts.googleapis.com/css2?family=Oswald:wght@700&family=Libre+Baskerville:wght@700&family=Tinos:wght@700&family=Noto+Sans:wght@400&display=swap">
<style>
  :root {
    --page-bg: #f7c64a;
    --card-black: #0b0b0b;
    --gold: #e2bd3c;
    --gold-dark: #a8852a;
    --pill-text: #f2e03a;
    --white: #ffffff;
    --photo-light: #e6e6e6;
    --photo-mid: #8a8a8a;
    --photo-dark: #151515;
  }
  * { box-sizing: border-box; margin: 0; padding: 0; }
  html, body { width: 1200px; height: 1000px; overflow: hidden; }
  body { background: var(--page-bg); position: relative; font-family: "Noto Sans", sans-serif; }

  .card { position: absolute; overflow: hidden; box-shadow: 6px 6px 10px rgba(0,0,0,0.25); }

  /* Front */
  .card-front { left: 171px; top: 95px; width: 847px; height: 405px; }
  .front-photo {
    position: absolute; inset: 0;
    background: linear-gradient(180deg, var(--photo-light) 0%, #cfcfcf 25%, var(--photo-mid) 50%, #2a2a2a 72%, var(--photo-dark) 100%);
  }
  .front-owner {
    position: absolute; right: 10px; top: 12px;
    font-family: "Libre Baskerville", serif; font-weight: 700; font-size: 22px; color: #111;
  }
  .front-title {
    position: absolute; left: 0; right: 0; top: 318px; text-align: center;
    font-family: "Oswald", sans-serif; font-weight: 700; font-size: 56px; line-height: 64px; letter-spacing: 0.5px;
    background: linear-gradient(180deg, #f5d653 0%, var(--gold) 50%, var(--gold-dark) 100%);
    -webkit-background-clip: text; background-clip: text; color: transparent;
  }

  /* Back */
  .card-back { left: 173px; top: 526px; width: 845px; height: 384px; background: var(--card-black); }
  .back-texture {
    position: absolute; inset: 0;
    background: linear-gradient(170deg, #1a1a1a 0%, #5a5a5a 28%, #cfcfcf 40%, #3c3c3c 52%, #7a7a7a 62%, #1c1c1c 80%, #444 100%);
  }
  .contact-oval {
    position: absolute; left: 25px; top: 10px; width: 790px; height: 120px;
    border-radius: 50%; background: var(--card-black); border: 2px solid var(--white);
    color: var(--white); text-align: center;
    display: flex; flex-direction: column; justify-content: center;
  }
  .contact-name { font-family: "Libre Baskerville", serif; font-weight: 700; font-size: 29px; line-height: 34px; letter-spacing: 1.5px; }
  .contact-address { font-family: "Tinos", serif; font-weight: 700; font-size: 23px; line-height: 30px; }
  .contact-phone { font-family: "Libre Baskerville", serif; font-weight: 700; font-size: 23px; line-height: 28px; letter-spacing: 2px; }

  .service {
    position: absolute; width: 410px; height: 60px;
    border: 2px solid var(--white); border-radius: 30px; background: var(--card-black);
    color: var(--pill-text); font-size: 23px; line-height: 28px; letter-spacing: 1.2px;
    text-align: center; display: flex; align-items: center; justify-content: center;
  }
  .col-left { left: 14px; }
  .col-right { left: 426px; }
  .row-1 { top: 160px; }
  .row-2 { top: 234px; }
  .row-3 { top: 310px; }
</style>
</head>
<body>
  <section class="card card-front">
    <div class="front-photo" role="img" aria-label="Black and white photo of wheat ears silhouetted against a bright sky"></div>
    <p class="front-owner">Morris Tulane</p>
    <h1 class="front-title">Toms Welding And Seed Cleaning</h1>
  </section>

  <section class="card card-back">
    <div class="back-texture" role="img" aria-label="Dark painted texture of a field in black and grey strokes"></div>
    <div class="contact-oval">
      <p class="contact-name">Morris Tulane</p>
      <p class="contact-address">ADD: 48213 W COUNTY RD 318, CEDAR BEND OK 73990</p>
      <p class="contact-phone">Phone: 555-441-9362</p>
    </div>
    <p class="service col-left row-1">Registered and certified<br>professionals.</p>
    <p class="service col-right row-1">Portable cleaners used<br>to clean wheat.</p>
    <p class="service col-left row-2">Get the cleaning done on<br>your farm itself.</p>
    <p class="service col-right row-2">Improve and build new<br>corrals in winters.</p>
    <p class="service col-left row-3">Build sheds, cattle<br>shelters, wind breaks, etc.</p>
    <p class="service col-right row-3">Other welding jobs<br>welcome.</p>
  </section>
</body>
</html>
```